High Tech Real Estate Startup needs a business card

We are developing an innovative real estate marketing product based around advanced search and virtual reality.

We talk to people, we need business cards.

Target Market(s)

The target market is technology professionals and realtors.

Contact Information for Business Card

The information to be included will include

Name
Title
Phone Number
E-mail Address
www.zelquin.com

It should use simple iconography for each one of those fields.

Font styles to use
Other font styles liked:
• Co, Jubilat, Avenir

Colors

Designer to choose colors to be used in the design.

Requirements
Must have
• Clean aesthetic,
• Good use of negative space.
• It should use our company logo, shown in the attached file. It is able to use the negative of that logo (coloured font and white background) and I have attached other acceptable accent colours in a swatch file.
Should not have
• Should not be too busy
• No extraneous text (slogans, tag lines etc)

```html
<!DOCTYPE html>
<html lang="en">
<head>
<meta charset="utf-8">
<title>Zelquin Business Card</title>
<link rel="stylesheet" href="https://fonts.googleapis.com/css2?family=Nunito+Sans:wght@300;400;600&display=swap">
<style>
  :root {
    --teal: #08b9bd;
    --white: #ffffff;
    --backdrop: #e4e4e2;
    --card-shadow: rgba(0, 0, 0, 0.18);
  }
  * { margin: 0; padding: 0; box-sizing: border-box; }
  html, body {
    width: 1200px;
    height: 1000px;
    overflow: hidden;
    background: var(--backdrop);
    font-family: "Nunito Sans", "Avenir", sans-serif;
  }
  .canvas { position: relative; width: 1200px; height: 1000px; }
  .card {
    position: absolute;
    border-radius: 40px;
    box-shadow: 0 8px 22px var(--card-shadow);
    overflow: hidden;
  }
  .card-front {
    left: 152px; top: 102px; width: 626px; height: 358px;
    background: var(--white);
    display: flex; align-items: center; justify-content: center;
  }
  .front-wordmark {
    color: var(--teal);
    font-size: 78px;
    font-weight: 600;
    letter-spacing: 2px;
    line-height: 1;
    margin-top: 4px;
  }
  .card-back {
    left: 372px; top: 548px; width: 634px; height: 362px;
    background: var(--teal);
    color: var(--white);
  }
  .person-name {
    position: absolute; left: 36px; top: 120px;
    font-size: 32px; font-weight: 400; line-height: 1;
  }
  .person-title {
    position: absolute; left: 36px; top: 163px;
    font-size: 19px; font-weight: 400; line-height: 1;
  }
  .title-rule {
    position: absolute; left: 190px; top: 177px;
    width: 409px; height: 2px; background: var(--white);
  }
  .contact-list {
    position: absolute; left: 36px; top: 230px;
    list-style: none;
  }
  .contact-item {
    display: flex; align-items: center;
    height: 29.5px;
    font-size: 21px; letter-spacing: 1.6px; line-height: 1;
  }
  .contact-icon { width: 20px; height: 20px; margin-right: 21px; flex: none; }
  .back-wordmark {
    position: absolute; right: 46px; top: 276px;
    font-size: 38px; font-weight: 600; letter-spacing: 1px; line-height: 1;
  }
</style>
</head>
<body>
<main class="canvas">
  <section class="card card-front" aria-label="Card front">
    <div class="front-wordmark">ZELQUIN</div>
  </section>

  <section class="card card-back" aria-label="Card back">
    <div class="person-name">Name of Person</div>
    <div class="person-title">Title of Person</div>
    <div class="title-rule"></div>

    <ul class="contact-list">
      <li class="contact-item">
        <svg class="contact-icon" viewBox="0 0 20 20" aria-hidden="true">
          <path fill="#fff" d="M4.2 2.5c.6-.5 1.4-.4 1.8.2l1.8 2.6c.4.6.3 1.3-.2 1.7l-1.1.9c.8 1.9 2.3 3.5 4.2 4.4l.9-1.1c.4-.5 1.2-.6 1.7-.2l2.6 1.8c.6.4.7 1.3.2 1.8l-1.4 1.6c-.6.7-1.6.9-2.5.6C7.4 15.3 4.4 12.3 2.9 7.5c-.3-.9 0-1.9.6-2.5z"/>
        </svg>
        <span>+123 456 7890</span>
      </li>
      <li class="contact-item">
        <svg class="contact-icon" viewBox="0 0 20 20" aria-hidden="true" fill="none" stroke="#fff" stroke-width="1.5">
          <circle cx="10" cy="10" r="8"/>
          <ellipse cx="10" cy="10" rx="3.6" ry="8"/>
          <line x1="2" y1="10" x2="18" y2="10"/>
          <path d="M3.5 5.8h13M3.5 14.2h13"/>
        </svg>
        <span>www.zelquin.com</span>
      </li>
      <li class="contact-item">
        <svg class="contact-icon" viewBox="0 0 20 20" aria-hidden="true">
          <rect x="2" y="5" width="16" height="11" fill="#fff"/>
          <path d="M2 5l8 6 8-6" fill="none" stroke="#08b9bd" stroke-width="1.4"/>
        </svg>
        <span>E-mail Address</span>
      </li>
    </ul>

    <div class="back-wordmark">ZELQUIN</div>
  </section>
</main>
</body>
</html>
```